Brimsett Gardening Fresh New Website

We are looking to create a simple fresh website for our landscaping business. The website should appeal to a 'high end' audience. We deal with a lot of Embassies and affluent clients who have extremely large gardens that are meticulously maintained. The site is about communicating our excellent landscaping and customer service skills and encouraging new clients to reach out and engage us to take care of their gardens.

The website is basically going to be our business card, it will have almost no functionality other than two 'contact us' forms, one for smaller clients and one for more detailed projects.

The website will not have a lot of written content and will have to show photos of beautifully landscaped gardens.

The main logo in black will influence the site, however, we are open to all suggestions.

We are expecting to have the following pages:
Home Page
Services
About Us
Contact Us
Showcase (photo gallery of our work)

We need someone who can code it to wordpress and be available for minor changes over a number of days. They will be simple tweaks.

```html
<!DOCTYPE html>
<html lang="en">
<head>
<meta charset="utf-8">
<title>Brimsett Gardening</title>
<link href="https://fonts.googleapis.com/css2?family=Cinzel:wght@400;500&family=Poppins:wght@400;500;600&display=swap" rel="stylesheet">
<style>
:root{
  --ink:#1c1a17;
  --gold:#a9782a;
  --gold-light:#c8a24a;
  --yellow:#f3d13f;
  --paper:#ffffff;
  --mist:#f4f4f4;
  --text:#555;
  --line:#ddd;
  --serif:'Cinzel', serif;
  --sans:'Poppins', sans-serif;
}
*{box-sizing:border-box;margin:0;padding:0}
html,body{width:1200px;height:3896px;overflow:hidden}
body{position:relative;font-family:var(--sans);color:var(--text);background:var(--paper)}
.abs{position:absolute}
.btn{position:absolute;display:flex;align-items:center;justify-content:center;background:var(--gold);color:#fff;font:500 12px var(--sans);text-transform:uppercase;letter-spacing:.3px}
.section-title{position:absolute;left:0;width:1200px;text-align:center;font:400 37px var(--serif);color:var(--ink);letter-spacing:1px}
.rule{position:absolute;height:2px;width:48px;background:var(--gold)}

/* header */
.site-header{left:0;top:0;width:1200px;height:85px;background:var(--ink)}
.brand{position:absolute;text-align:center;font-family:var(--serif);color:var(--gold-light);letter-spacing:4px;line-height:1.1}
.nav a{position:absolute;top:33px;font:400 13px var(--sans);color:#fff;text-decoration:none}
.nav a.current{color:var(--yellow)}

/* hero */
.hero{left:0;top:85px;width:1200px;height:545px;background:linear-gradient(180deg,#6f7a77 0%,#8a9386 28%,#4e6b32 55%,#4f7a2a 78%,#3f6421 100%)}
.hero-tag{left:142px;top:222px;width:271px;height:50px;background:#fff;border-left:4px solid var(--gold);font:600 24px var(--sans);color:#3a3a3a;display:flex;align-items:center;padding-left:14px;letter-spacing:.3px}
.hero-title{left:142px;top:284px;font:400 41px/51px var(--serif);color:#fff;letter-spacing:1px}

.quick{left:710px;top:106px;width:349px;height:507px;background:rgba(236,236,230,.95)}
.tabs{position:absolute;left:0;top:3px;width:349px;height:36px}
.tab{position:absolute;top:0;height:36px;display:flex;align-items:center;justify-content:center;font:500 12px var(--sans);text-transform:uppercase}
.quick h3{position:absolute;top:52px;left:0;width:349px;text-align:center;font:400 19px var(--serif);color:#333;letter-spacing:1px}
.field{position:absolute;left:18px;width:313px;background:#fff;border:1px solid #e2e2e2;border-radius:3px;font:400 11px var(--sans);color:#888;padding:11px 10px}
.field svg{position:absolute;right:10px;top:12px}
.check{position:absolute;font:400 10px var(--sans);color:#333;display:flex;align-items:center;gap:8px}
.check i{display:inline-block;width:11px;height:11px;border:1px solid #ccc;background:#fff}
.check i.on{background:var(--yellow);border-color:var(--gold)}

/* about */
.about-photo{left:121px;top:666px;width:507px;height:451px;background:radial-gradient(ellipse at 50% 55%,#6f9a52 0%,#9cb98a 45%,rgba(255,255,255,0) 75%)}
.about-kicker{left:611px;top:752px;font:400 33px var(--serif);color:var(--gold)}
.about-title{left:611px;top:790px;font:400 33px var(--serif);color:var(--ink);letter-spacing:1px}
.about-copy{left:611px;top:862px;width:450px;font:400 13px/22px var(--sans);color:#555}
.about-copy p+p{margin-top:6px}

/* services */
.services{left:0;top:1171px;width:1200px;height:947px;background:var(--mist)}
.service-card{position:absolute;width:300px;height:241px;border-radius:4px;overflow:hidden}
.service-card .label{position:absolute;left:0;right:0;bottom:38px;text-align:center;color:#fff;font:500 15px var(--sans)}
.service-card .sub{position:absolute;left:0;right:0;bottom:18px;text-align:center;color:#fff;font:400 12px var(--sans);text-decoration:underline}

/* testimonials */
.testimonials{left:0;top:2118px;width:1200px;height:533px;background:linear-gradient(160deg,#2f3b22 0%,#46602c 40%,#35471f 70%,#28331a 100%)}
.quote-card{position:absolute;background:#fff;border-radius:4px;padding:0 22px}
.avatar{position:absolute;left:22px;width:60px;height:60px;border-radius:50%}
.quote-card .name{position:absolute;left:92px;font:500 15px var(--sans);color:#222}
.stars{position:absolute;left:92px;display:flex;gap:3px}
.quote-card .body{position:absolute;left:22px;right:16px;font:400 12.5px/22px var(--sans);color:#555}
.arrow{position:absolute;width:44px;height:44px;border-radius:50%;border:1.5px solid #fff;display:flex;align-items:center;justify-content:center}

/* gallery */
.tile{position:absolute;width:300px}
.tile-note{background:var(--yellow);display:flex;align-items:center;justify-content:center;text-align:center;padding:0 56px;font:400 13px/22px var(--sans);color:#3a3320}

/* footer */
.site-footer{left:0;top:3519px;width:1200px;height:377px;background:var(--ink)}
.foot-head{position:absolute;font:400 16px var(--serif);color:#fff;letter-spacing:1px}
.foot-head::after{content:"";position:absolute;left:0;top:28px;width:135px;height:1px;background:#555}
.foot-link{position:absolute;font:400 12px var(--sans);color:#fff}
.social{position:absolute;top:3771px;width:27px;height:27px;border:1.5px solid #fff;border-radius:50%}
.contact-item{position:absolute;left:849px;font:400 12.5px/19px var(--sans);color:#fff;display:flex;gap:10px}
.contact-item b{font-weight:500;display:block}
</style>
</head>
<body>

<header class="abs site-header">
  <div class="brand" style="left:128px;top:22px;width:114px;font-size:14px">BRIMSETT<br><span style="font-size:9px;letter-spacing:3px">GARDENING</span></div>
  <nav class="nav">
    <a class="current" style="left:434px">Home</a>
    <a style="left:513px">About Us</a>
    <a style="left:613px">Services</a>
    <a style="left:707px">Gallery</a>
    <a style="left:791px">Contact Us</a>
  </nav>
  <div class="btn" style="left:905px;top:26px;width:154px;height:33px">Request a Quote</div>
</header>

<section class="abs hero" role="img" aria-label="Manicured lawn with trees in front of city buildings"></section>
<div class="abs hero-tag">BRIMSETT GARDENING</div>
<h1 class="abs hero-title">YOUR FULL<br>LANDSCAPING &amp; LAWN<br>CARE EXPERTS</h1>
<div class="btn" style="left:142px;top:451px;width:153px;height:38px">Request a Quote</div>

<form class="abs quick">
  <div class="tabs">
    <div class="tab" style="left:0;width:190px;background:var(--yellow);color:#333;border-radius:0 0 0 18px">Smaller Clients</div>
    <div class="tab" style="left:180px;width:150px;background:var(--gold);color:#fff;border-radius:0 18px 0 0">Large Clients</div>
  </div>
  <h3>QUICK CONTACT</h3>
  <div class="field" style="top:85px;height:39px">Name<svg width="14" height="14" viewBox="0 0 14 14" fill="none" stroke="#aaa"><circle cx="7" cy="5" r="3"/><path d="M2 13c1-3 9-3 10 0"/></svg></div>
  <div class="field" style="top:133px;height:39px">Email<svg width="14" height="14" viewBox="0 0 14 14" fill="none" stroke="#aaa"><rect x="1.5" y="3" width="11" height="9"/><path d="M1.5 3l5.5 5 5.5-5"/></svg></div>
  <div class="field" style="top:181px;height:40px">Phone<svg width="14" height="14" viewBox="0 0 14 14" fill="none" stroke="#aaa"><path d="M3 1.5l2.5 3-1.5 1.5c1 2 2.5 3.5 4.5 4.5l1.5-1.5 3 2.5-1.5 2C6 13 1 8 1 3.5z"/></svg></div>
  <div class="field" style="top:230px;height:38px">Service Type<svg width="10" height="10" viewBox="0 0 10 10" fill="none" stroke="#aaa"><path d="M2 4l3 3 3-3"/></svg></div>
  <div class="field" style="top:278px;height:99px">Message</div>
  <div class="check" style="left:18px;top:386px"><i></i>Weekly Lawn Maintenance</div>
  <div class="check" style="left:202px;top:386px"><i></i>Spring Clean Up</div>
  <div class="check" style="left:18px;top:408px"><i class="on"></i>Fertilizer/weed Control</div>
  <div class="check" style="left:202px;top:408px"><i></i>Fall Clean Up</div>
  <div class="check" style="left:18px;top:431px"><i></i>Core Aeration</div>
  <div class="btn" style="left:18px;top:451px;width:313px;height:39px;font-size:14px;border-radius:3px">Submit</div>
</form>

<div class="abs about-photo" role="img" aria-label="Landscaped park lawn framed in a soft vignette"></div>
<h2 class="abs about-kicker">ABOUT</h2>
<h2 class="abs about-title">BRIMSETT GARDENING</h2>
<div class="rule" style="left:611px;top:843px"></div>
<div class="abs about-copy">
  <p>Duis aute irure dolor in reprehenderit in voluptate velit esse cillum dolore eu fugiat nulla pariatur.</p>
  <p>Lorem ipsum dolor sit amet, consectetur adipiscing elit, sed do amit eiusmod tempor incididunt ut labore et dolore magna aliqua. Ut enim ad minim veniam, quis nostrud exercitation ullamco laboris nisi ut aliquip ex ea commodo consequat.</p>
</div>
<div class="btn" style="left:611px;top:1021px;width:153px;height:34px">Read More</div>

<section class="abs services"></section>
<h2 class="section-title" style="top:1248px">OUR SERVICES</h2>
<div class="rule" style="left:576px;top:1303px"></div>
<div class="btn" style="left:437px;top:1327px;width:159px;height:35px;background:var(--yellow);color:#333">Landscape Service</div>
<div class="btn" style="left:602px;top:1327px;width:159px;height:35px">Lawn Service</div>

<div class="service-card" style="left:141px;top:1393px;background:linear-gradient(180deg,#8fb3d8 0%,#5c7a4a 45%,#2a3a1e 85%,#161a12 100%)" role="img" aria-label="Estate house with landscaped grounds"><div class="label">Design Service</div></div>
<div class="service-card" style="left:449px;top:1393px;background:linear-gradient(180deg,#9aa46a 0%,#4e7a2c 45%,#2a3a1a 85%,#141612 100%)" role="img" aria-label="Sunlit garden path between lawns"><div class="label" style="bottom:42px">Mulch or Rock Install</div><div class="sub">Get A Estimate →</div></div>
<div class="service-card" style="left:758px;top:1393px;background:linear-gradient(180deg,#5a4636 0%,#3e3126 55%,#1d1812 100%)" role="img" aria-label="Soil with pots and a hand trowel"><div class="label">Grading Rough</div></div>
<div class="service-card" style="left:141px;top:1710px;background:linear-gradient(180deg,#b76a8e 0%,#5e8a3c 40%,#3e6024 75%,#151a10 100%)" role="img" aria-label="Curved path through flowering shrubs"><div class="label">Grading</div></div>
<div class="service-card" style="left:449px;top:1710px;background:linear-gradient(180deg,#4a6a2c 0%,#6b5a3c 40%,#3d4a22 75%,#14170f 100%)" role="img" aria-label="Rolls of sod being laid"><div class="label">Sod Installation</div></div>
<div class="service-card" style="left:758px;top:1710px;background:linear-gradient(180deg,#b8c0b2 0%,#5f7a46 40%,#33461f 75%,#141610 100%)" role="img" aria-label="Hedged garden with iron railing"><div class="label">Retaining Walls</div></div>
<div class="btn" style="left:522px;top:1999px;width:154px;height:34px">Request a Quote</div>

<section class="abs testimonials" role="img" aria-label="Aerial view of green landscaped grounds"></section>
<h2 class="section-title" style="top:2194px;color:#fff">WHAT OUR CLIENTS SAY</h2>
<div class="arrow" style="left:75px;top:2431px"><svg width="12" height="12" viewBox="0 0 12 12" fill="none" stroke="#fff" stroke-width="2"><path d="M8 2L4 6l4 4"/></svg></div>
<div class="arrow" style="left:1082px;top:2431px"><svg width="12" height="12" viewBox="0 0 12 12" fill="none" stroke="#fff" stroke-width="2"><path d="M4 2l4 4-4 4"/></svg></div>

<div class="quote-card" style="left:141px;top:2300px;width:299px;height:268px">
  <div class="avatar" style="top:22px;background:#6aa7c8"></div>
  <div class="name" style="top:30px">Owen Carrow</div>
  <div class="stars" style="top:54px"><svg width="72" height="12" viewBox="0 0 72 12" fill="#f5c518"><path id="s" d="M6 0l1.8 3.9 4.2.4-3.2 2.8 1 4.1L6 9 2.2 11.2l1-4.1L0 4.3l4.2-.4z"/><use href="#s" x="15"/><use href="#s" x="30"/><use href="#s" x="45"/><use href="#s" x="60"/></svg></div>
  <div class="body" style="top:99px">Lorem ipsum dolor sit amet, consectetur adipiscing elit, sed do eiusmod tempor incididunt ut labore et dolore magna aliqua. Ut enim ad minim veniam ut aut reiciendis voluptatibus maiores alias ut aut reiciendis voluptatibus.</div>
</div>
<div class="quote-card" style="left:449px;top:2271px;width:300px;height:275px;border-bottom:6px solid var(--gold)">
  <div class="avatar" style="top:18px;left:20px;background:#8a6b58"></div>
  <div class="name" style="top:26px;left:92px">Lena Marsh</div>
  <div class="stars" style="top:50px"><svg width="72" height="12" viewBox="0 0 72 12" fill="#f5c518"><use href="#s"/><use href="#s" x="15"/><use href="#s" x="30"/><use href="#s" x="45"/><use href="#s" x="60"/></svg></div>
  <div class="body" style="top:88px">Sed ut perspiciatis unde omnis iste natus error sit voluptatem accusantium doloremque laudantium, totam rem aperiam, eaque ipsa quae ab illo AMIT inventore veritatis et quasi architecto beatae vitae dicta sunt explicabo. Nemo enim ipsam voluptatem.</div>
</div>
<div class="quote-card" style="left:758px;top:2300px;width:300px;height:268px">
  <div class="avatar" style="top:22px;background:#3a4a44"></div>
  <div class="name" style="top:30px">Theo R</div>
  <div class="stars" style="top:54px"><svg width="72" height="12" viewBox="0 0 72 12" fill="#f5c518"><use href="#s"/><use href="#s" x="15"/><use href="#s" x="30"/><use href="#s" x="45"/><use href="#s" x="60"/></svg></div>
  <div class="body" style="top:99px">Lorem ipsum dolor sit amet, consectetur adipiscing elit, sed do eiusmod tempor incididunt ut labore et dolore magna aliqua. Ut enim ad minim veniam ut aut reiciendis voluptatibus maiores alias ut aut reiciendis voluptatibus.</div>
</div>

<h2 class="section-title" style="top:2726px">WORK GALLERY</h2>
<div class="rule" style="left:576px;top:2781px"></div>
<div class="tile" style="left:141px;top:2834px;height:268px;background:linear-gradient(180deg,#c9d2d6 0%,#8a8a7a 35%,#4f7a2c 65%,#3f6a22 100%)" role="img" aria-label="Grand hotel with formal lawn"></div>
<div class="tile" style="left:141px;top:3111px;height:266px;background:linear-gradient(160deg,#e8eef0 0%,#9fc06a 40%,#5c8a34 70%,#3f6a22 100%)" role="img" aria-label="Sunlit park lawn with trees"></div>
<div class="tile tile-note" style="left:449px;top:2805px;height:269px">Itaque earum rerum hic tenetur a sapiente delectus, ut aut reiciendis voluptatibus maiores alias consequatur aut perferendis doloribus asperiores repellat.</div>
<div class="tile" style="left:449px;top:3082px;height:266px;background:linear-gradient(180deg,#4f6a30 0%,#a2485a 30%,#8a7a66 60%,#6a5e50 100%)" role="img" aria-label="Stone path through flower beds"></div>
<div class="tile" style="left:758px;top:2834px;height:268px;background:linear-gradient(180deg,#cfe0ee 0%,#a98a6a 35%,#7aa63a 65%,#5e8a26 100%)" role="img" aria-label="Villas above a sloping green lawn"></div>
<div class="tile" style="left:758px;top:3111px;height:266px;background:linear-gradient(180deg,#b9c2c6 0%,#5f7a3a 40%,#a56aa0 75%,#4f7a2a 100%)" role="img" aria-label="Office building with tree and flower border"></div>
<div class="btn" style="left:522px;top:3400px;width:153px;height:33px">View All</div>

<footer class="abs site-footer"></footer>
<div class="brand" style="left:130px;top:3680px;width:210px;font-size:26px;letter-spacing:8px">BRIMSETT<br><span style="font-size:16px;letter-spacing:8px">GARDENING</span></div>
<div class="social" style="left:169px"></div>
<div class="social" style="left:204px"></div>
<div class="social" style="left:239px"></div>
<div class="social" style="left:272px"></div>

<div class="foot-head" style="left:517px;top:3574px">QUICK LINKS</div>
<div class="foot-link" style="left:517px;top:3623px">Home</div>
<div class="foot-link" style="left:517px;top:3664px">Services</div>
<div class="foot-link" style="left:517px;top:3705px">Gallery</div>
<div class="foot-link" style="left:517px;top:3744px">About Us</div>
<div class="foot-link" style="left:517px;top:3785px">contact Us</div>

<div class="foot-head" style="left:849px;top:3574px">CONTACT DETAILS</div>
<div class="contact-item" style="top:3617px"><svg width="26" height="26" viewBox="0 0 26 26" fill="none" stroke="#fff"><path d="M13 3a7 7 0 017 7c0 5-7 13-7 13S6 15 6 10a7 7 0 017-7z"/><circle cx="13" cy="10" r="2.5"/></svg><span>123, Building Name, Street<br>City, State XY 123456</span></div>
<div class="contact-item" style="top:3688px"><svg width="26" height="26" viewBox="0 0 26 26" fill="none" stroke="#fff"><path d="M6 4l4 5-2 2c1.5 3 4 5.5 7 7l2-2 5 4-2 3C11 23 3 15 3 7z"/></svg><span><b>Phone</b>(123) 456-7890</span></div>
<div class="contact-item" style="top:3761px"><svg width="26" height="26" viewBox="0 0 26 26" fill="none" stroke="#fff"><rect x="3" y="7" width="20" height="14"/><path d="M3 7l10 8 10-8"/></svg><span><b>Email</b>info@brimsettgardening.com</span></div>

<div class="abs" style="left:141px;top:3855px;width:918px;height:1px;background:#444"></div>
<div class="abs" style="left:0;top:3868px;width:1200px;text-align:center;font:400 12px var(--sans);color:#ddd">© 2024 Brimsett Gardening. All Rights Reserved</div>

</body>
</html>
```